Colin Vardek Business card

Hey there, I’m hoping to have a business card designed. I’m in Real estate and just switched to a new Brokerage called: The Harbourline Property Group

The back could just be the company name maybe or whatever looks good!

I’ve attached some logos of our company and some cards my buddy had done up.

On the card:
Colin Vardek
colinvardek@mailora.com
587-412-9065
colinvardek.ca

Target Market(s)

Home buyers and sellers

Industry/Entity Type

Real Estate

Contact Information for Business Card

just looking for a cool and modern design with my picture on it. I like the idea of Black and red being used.

Requirements
Must have
• all the details provided. I'm open to anything. Just want a professional looking card.

```html
<!DOCTYPE html>
<html lang="en">
<head>
<meta charset="UTF-8">
<title>Colin Vardek – Business Card</title>
<link href="https://fonts.googleapis.com/css2?family=Poppins:wght@400;500;700&display=swap" rel="stylesheet">
<style>
  :root {
    --stage: #1c1c1c;
    --card: #0c0c0d;
    --card-edge: #1a1a1b;
    --red: #d7193a;
    --white: #ffffff;
    --photo-dark: #141518;
    --photo-mid: #2a3038;
  }
  * { box-sizing: border-box; margin: 0; padding: 0; }
  html, body {
    width: 1200px; height: 1015px; overflow: hidden;
    background: var(--stage);
    font-family: "Poppins", sans-serif;
  }
  .canvas {
    position: relative; width: 1200px; height: 1015px;
    display: flex; flex-direction: column; align-items: center; justify-content: center; gap: 60px;
  }
  .card {
    position: relative; width: 630px; height: 360px;
    background: var(--card);
    border-bottom: 4px solid var(--red);
    overflow: hidden;
    box-shadow: 0 18px 40px rgba(0,0,0,0.55);
  }
  /* back */
  .card-back { display: flex; align-items: center; justify-content: flex-end; padding-right: 56px; }
  .brand-name {
    color: var(--white); font-weight: 700; font-size: 30px; line-height: 1.1;
    text-align: right; letter-spacing: 0.5px;
  }
  /* front */
  .portrait {
    position: absolute; left: 40px; bottom: 0; width: 300px; height: 300px;
    background: radial-gradient(ellipse at 45% 35%, var(--photo-mid) 0%, var(--photo-dark) 70%, var(--card) 100%);
  }
  .details {
    position: absolute; right: 40px; top: 38px; width: 290px;
    display: flex; flex-direction: column; align-items: center; text-align: center;
  }
  .details .brand-name { font-size: 22px; text-align: center; }
  .agent-name {
    margin-top: 40px; color: var(--red); font-weight: 500; font-size: 26px;
    text-transform: uppercase; letter-spacing: 1px;
  }
  .icon-rule { display: flex; align-items: center; width: 230px; margin: 10px 0 14px; }
  .icon-rule .line { flex: 1; height: 1.5px; background: var(--red); }
  .icon-rule .icons { display: flex; gap: 4px; padding: 0 6px; }
  .icon-dot { width: 26px; height: 26px; border-radius: 50%; background: var(--red); display: flex; align-items: center; justify-content: center; }
  .contact { color: var(--white); font-size: 17px; line-height: 1.45; }
</style>
</head>
<body>
<main class="canvas">
  <section class="card card-back">
    <p class="brand-name">The Harbourline<br>Property Group</p>
  </section>

  <section class="card card-front">
    <div class="portrait" role="img" aria-label="Portrait photo of Colin Vardek in a dark suit and white shirt"></div>
    <div class="details">
      <p class="brand-name">The Harbourline<br>Property Group</p>
      <h1 class="agent-name">Colin Vardek</h1>
      <div class="icon-rule">
        <span class="line"></span>
        <div class="icons">
          <span class="icon-dot">
            <svg width="14" height="14" viewBox="0 0 24 24" fill="none" stroke="#fff" stroke-width="2.2" stroke-linecap="round" stroke-linejoin="round"><path d="M22 16.9v3a2 2 0 0 1-2.2 2 19.8 19.8 0 0 1-8.6-3.1 19.5 19.5 0 0 1-6-6A19.8 19.8 0 0 1 2.1 4.2 2 2 0 0 1 4.1 2h3a2 2 0 0 1 2 1.7c.1.9.4 1.8.7 2.7a2 2 0 0 1-.5 2.1L8 9.8a16 16 0 0 0 6 6l1.3-1.3a2 2 0 0 1 2.1-.4c.9.3 1.8.6 2.7.7a2 2 0 0 1 1.7 2z"/></svg>
          </span>
          <span class="icon-dot">
            <svg width="14" height="14" viewBox="0 0 24 24" fill="none" stroke="#fff" stroke-width="2.2" stroke-linejoin="round"><rect x="3" y="5" width="18" height="14" rx="1"/><path d="M3 6l9 7 9-7"/></svg>
          </span>
          <span class="icon-dot">
            <svg width="14" height="14" viewBox="0 0 24 24" fill="none" stroke="#fff" stroke-width="2"><circle cx="12" cy="12" r="9"/><path d="M3 12h18M12 3c3 3.2 3 14.8 0 18M12 3c-3 3.2-3 14.8 0 18"/></svg>
          </span>
        </div>
        <span class="line"></span>
      </div>
      <p class="contact">587-412-9065<br>colinvardek@mailora.com<br>colinvardek.ca</p>
    </div>
  </section>
</main>
</body>
</html>
```